Valdo Capital

We need a corporate style website design for a new company based in Shenzhen's Qianhai Special Economic Development Zone, China. We provide a range of financial services to large international investment companies. Typically these companies invest over 5 million RMB. The company is part of a group that consists of NorthKilns, ValdoTrusts and ValdoEquity. Our location and gateway into Qianhai Special Economic Zone is our core advantage. We would like to see designs that Do Not use purple and orange. The website design should be similar to other websites in this family but different enough to give it a unique style (See attached website links for reference). The final design should communicate financial safety and growth. This website will act partly as a business chamber with connections to the government so we would like it to be diplomatic in style.

www.northkilns.example
www.valdotrusts.example

*Nevegation Bar
Should including Homepage, Financial Product, Team, News.
Could refer to www.valdotrusts.example

*Contact Details

Miss Lan
Address:E 728, North Block, KMO Centre, East Sector, Shenzhen Bright Science Campus
Telephone: +86 0755 63920417
Cellphone: +86 13957280316

* Social Media
Should be grouped like:
1. Weibo QRcode+ Weibo
2. Facebook, Twitter, Linkedin.

Industry/Entity Type

Investment

```html
<!DOCTYPE html>
<html lang="en">
<head>
<meta charset="utf-8">
<title>Valdo Capital</title>
<link href="https://fonts.googleapis.com/css2?family=Open+Sans:wght@300;400;600&display=swap" rel="stylesheet">
<style>
:root{
  --blue:#1a9be0;
  --blue-dark:#0c7fc4;
  --ink:#333;
  --muted:#666;
  --line:#e2e2e2;
  --footer:#262626;
  --footer-bottom:#303030;
  --footer-text:#ffffff;
  --white:#fff;
}
*{box-sizing:border-box;margin:0;padding:0}
html,body{width:781px;height:1200px;overflow:hidden;background:var(--white)}
body{position:relative;font-family:"Open Sans",Arial,sans-serif;color:var(--ink)}
.abs{position:absolute}
a{color:inherit;text-decoration:none}

/* header */
.site-header{left:0;top:0;width:781px;height:66px;border-bottom:1px solid var(--line)}
.brand{left:73px;top:16px;display:flex;align-items:center;gap:8px}
.brand-mark{width:26px;height:26px;border-radius:50%;background:var(--blue-dark)}
.brand-name{font-size:18px;font-weight:400;color:#1c2a44;letter-spacing:.2px}
.main-nav{left:334px;top:28px;display:flex;align-items:center;font-size:9px;color:#333}
.main-nav a{margin-right:24px}
.main-nav .active{background:#35b6f0;color:var(--white);padding:4px 9px;margin-right:20px}

/* hero */
.hero{left:0;top:66px;width:781px;height:440px;background:linear-gradient(160deg,#b7c7d4 0%,#6f8196 30%,#3a4658 60%,#5a4a3c 85%,#2b3240 100%)}
.hero-panel{left:0;top:66px}
.hero-title{left:49px;top:182px;font-size:19px;font-weight:300;line-height:22px;color:#333}
.hero-title strong{color:var(--blue);font-weight:400}
.hero-list{left:50px;top:245px;list-style:none;font-size:8px;color:#333}
.hero-list li{display:flex;align-items:center;height:23px}
.hero-list svg{margin-right:7px}
.hero-more{left:51px;top:347px;font-size:9px;color:var(--blue-dark);text-decoration:underline}
.know-more{left:58px;top:410px}

/* services */
.services{left:71px;top:506px;width:639px;height:257px;border:1px solid #ececec;border-top:none;background:var(--white)}
.services-tab{left:338px;top:506px;width:104px;height:44px;border-radius:0 0 52px 52px;background:linear-gradient(#2aaef0,#0f86d3);color:var(--white);text-align:center;font-size:14px;padding-top:6px}
.services-tab span{display:block;font-size:8px;line-height:8px;opacity:.8}
.service{top:565px;width:137px;text-align:center}
.service-img{width:137px;height:87px;border:1px solid #ddd}
.service h3{font-size:11px;font-weight:400;margin-top:12px;color:#333}
.service h3.hl{color:var(--blue)}
.service p{font-size:7px;line-height:10.5px;color:#555;margin:6px 4px 0}
.btn{display:inline-block;background:var(--blue);color:var(--white);font-size:8px;border:1px solid #0a6fb0}
.service .btn{margin-top:8px;width:55px;height:18px;line-height:16px}
.slide-arrow{top:597px;width:22px;height:22px;background:var(--blue)}
.services-shadow{left:88px;top:760px;width:608px;height:8px;border-radius:50%;background:radial-gradient(ellipse at center,rgba(0,0,0,.55),rgba(0,0,0,0) 70%)}

/* about */
.about-title{left:75px;top:815px;font-size:12px;font-weight:400}
.about-text{left:76px;top:836px;width:316px;font-size:8px;line-height:13px;color:#444}
.about-btn{left:76px;top:950px;width:65px;height:21px;line-height:19px;text-align:center}

/* blog */
.blog-title{left:492px;top:815px;font-size:12px;font-weight:400}
.view-all{left:680px;top:820px;font-size:6.5px;font-style:italic;color:var(--blue)}
.blog-rule{left:492px;top:833px;width:216px;height:1px;background:var(--line)}
.avatar{left:427px;top:838px;width:60px;height:60px;border-radius:50%;border:3px solid #eee;background:radial-gradient(circle at 50% 45%,#c99a80,#6b4a3a)}
.blog-card{left:481px;top:840px;width:227px;height:112px;background:#f4f4f4;border:1px solid #e5e5e5;padding:9px 10px 0 21px}
.blog-head{display:flex;justify-content:space-between;align-items:center}
.blog-name{font-size:10px;color:#333}
.blog-date{font-size:6px;color:#888;display:flex;align-items:center;gap:4px}
.blog-text{font-size:7.5px;line-height:10.5px;color:#8a8a8a;margin-top:5px;text-align:justify}
.blog-foot{position:absolute;left:21px;right:10px;bottom:6px;display:flex;justify-content:space-between;font-size:6.5px;color:#999}

/* footer */
.footer{left:0;top:997px;width:781px;height:165px;background:var(--footer)}
.footer-text{color:var(--footer-text)}
.footer-mark{left:127px;top:1008px;width:36px;height:36px;border-radius:50%;background:#1c6fa6}
.footer-name{left:82px;top:1064px;width:132px;text-align:center;font-size:17px;letter-spacing:.3px}
.social{left:80px;top:1116px;display:flex;gap:5px}
.social i{width:18px;height:18px;border-radius:50%;background:var(--white)}
.footer-heading{font-size:11px;font-weight:600;color:var(--footer-text)}
.sitemap{left:271px;top:1024px}
.sitemap ul{list-style:none;font-size:8px;line-height:10.5px;margin-top:10px}
.divider{top:1025px;width:1px;height:88px;background:#3d3d3d}
.contact{left:393px;top:1024px;width:120px}
.contact-row{display:flex;align-items:flex-start;font-size:8px;line-height:10.5px;margin-top:4px}
.contact-row svg{flex:none;margin:1px 7px 0 0}
.contact .first{margin-top:10px}
.find-us{left:539px;top:1024px}
.map{left:539px;top:1045px;width:168px;height:108px;background:linear-gradient(135deg,#e8e6df,#d9d6cc);border:1px solid #fff}
.footer-bottom{left:0;top:1162px;width:781px;height:38px;background:var(--footer-bottom);color:#ddd;font-size:8px;text-align:center;line-height:38px}
</style>
</head>
<body>

<header class="site-header abs">
  <div class="brand abs"><span class="brand-mark"></span><span class="brand-name">Valdo Capital</span></div>
  <nav class="main-nav abs">
    <a class="active" href="#">HOME</a><a href="#">About Us</a><a href="#">Financial Product</a><a href="#">Team</a><a href="#">News</a><a href="#">Valdo Blog</a>
  </nav>
</header>

<section class="hero abs" role="img" aria-label="Aerial photograph of a city skyline at dusk with towers and lights"></section>
<svg class="hero-panel abs" width="300" height="440" viewBox="0 0 300 440">
  <polygon points="0,38 212,78 278,232 212,402 0,440" fill="#fff" fill-opacity=".86"/>
</svg>
<h1 class="hero-title abs"><strong>Valdo Capital</strong> is the<br>Key to Success</h1>
<ul class="hero-list abs">
  <li><svg width="12" height="13" viewBox="0 0 12 13"><polygon points="6,1 11,3.7 11,9.3 6,12 1,9.3 1,3.7" fill="#e6f4fb" stroke="#49a9dd"/></svg>Lorem ipsum dolor sit amet.</li>
  <li><svg width="12" height="13" viewBox="0 0 12 13"><polygon points="6,1 11,3.7 11,9.3 6,12 1,9.3 1,3.7" fill="#e6f4fb" stroke="#49a9dd"/></svg>Lorem ipsum dolor sit amet consectetur .</li>
  <li><svg width="12" height="13" viewBox="0 0 12 13"><polygon points="6,1 11,3.7 11,9.3 6,12 1,9.3 1,3.7" fill="#e6f4fb" stroke="#49a9dd"/></svg>Lorem ipsum dolor sit amet.</li>
  <li><svg width="12" height="13" viewBox="0 0 12 13"><polygon points="6,1 11,3.7 11,9.3 6,12 1,9.3 1,3.7" fill="#e6f4fb" stroke="#49a9dd"/></svg>Lorem ipsum dolor sit amet consectetur .</li>
</ul>
<a class="hero-more abs" href="#">Read More</a>
<svg class="know-more abs" width="78" height="78" viewBox="0 0 78 78">
  <defs><linearGradient id="kg" x1="0" y1="0" x2="0" y2="1"><stop offset="0" stop-color="#2bb4f3"/><stop offset="1" stop-color="#0b80cf"/></linearGradient></defs>
  <polygon points="39,2 72,20 72,58 39,76 6,58 6,20" fill="url(#kg)"/>
  <text x="38" y="36" text-anchor="middle" font-family="Open Sans, sans-serif" font-size="9.5" font-weight="600" fill="#fff">Want to</text>
  <text x="38" y="47" text-anchor="middle" font-family="Open Sans, sans-serif" font-size="9.5" font-weight="600" fill="#fff">know More</text>
</svg>

<section class="services abs"></section>
<div class="services-tab abs">Services<span>↑</span></div>

<article class="service abs" style="left:88px">
  <div class="service-img" role="img" aria-label="Photograph of business people shaking hands in an office" style="background:linear-gradient(#dfe6ec,#5b6470)"></div>
  <h3 class="hl">Consultancy</h3>
  <p>Lorem Ipsum is simply dummy text of the printing and typesetting industry.</p>
  <a class="btn" href="#">Read More</a>
</article>
<article class="service abs" style="left:243px">
  <div class="service-img" role="img" aria-label="Photograph of hands sheltering stacked coins with a small plant" style="background:linear-gradient(#f4f4f2,#d8cdb3)"></div>
  <h3>Finance</h3>
  <p>Lorem Ipsum is simply dummy text of the printing and typesetting industry.</p>
  <a class="btn" href="#">Read More</a>
</article>
<article class="service abs" style="left:399px">
  <div class="service-img" role="img" aria-label="Photograph of a house model on architectural plans" style="background:linear-gradient(#eceff1,#a9b0b6)"></div>
  <h3>Property Management</h3>
  <p>Lorem Ipsum is simply dummy text of the printing and typesetting industry.</p>
  <a class="btn" href="#">Read More</a>
</article>
<article class="service abs" style="left:555px">
  <div class="service-img" role="img" aria-label="Photograph of a hand holding house keys and a small house model" style="background:linear-gradient(#f2f2f2,#c9c2bb)"></div>
  <h3>Theme Real Estate</h3>
  <p>Lorem Ipsum is simply dummy text of the printing and typesetting industry.</p>
  <a class="btn" href="#">Read More</a>
</article>
<svg class="slide-arrow abs" style="left:84px" viewBox="0 0 22 22"><polygon points="13,7 8,11 13,15" fill="#fff"/></svg>
<svg class="slide-arrow abs" style="left:675px" viewBox="0 0 22 22"><polygon points="9,7 14,11 9,15" fill="#fff"/></svg>
<div class="services-shadow abs"></div>

<h2 class="about-title abs">About Us</h2>
<p class="about-text abs">Lorem Ipsum is simply dummy text of the printing and typesetting industry. Lorem Ipsum has been the industry's standard dummy text ever since the 1500s, when an unknown printer took a galley of type and scrambled it to make a type specimen book. It has survived not only five centuries, but also the leap into electronic typesetting, remaining essentially unchanged. It was popularised in the 1960s with the release of Letraset sheets containing Lorem Ipsum passages, and more recently with desktop publishing software like Aldus PageMaker including versions of Lorem Ipsum.</p>
<a class="btn about-btn abs" href="#">Read More</a>

<h2 class="blog-title abs">Our Blog</h2>
<a class="view-all abs" href="#">View All</a>
<div class="blog-rule abs"></div>
<div class="blog-card abs">
  <div class="blog-head">
    <span class="blog-name">Marina Solte</span>
    <span class="blog-date"><svg width="9" height="8" viewBox="0 0 9 8"><rect x=".5" y="1" width="8" height="6.5" fill="none" stroke="#999"/><line x1=".5" y1="3" x2="8.5" y2="3" stroke="#999"/></svg>30 Aralık 2012, Pazar</span>
  </div>
  <p class="blog-text">Lorem ipsum dolor sit amet, consectetur adipiscing elit. In pretium sollicitudin nisl, molestie aliquam nisi rutrum at. Sed sollicitudin vehicula metus, eget elementum lectus facilisis vel. Integer vel fringilla magna.</p>
  <div class="blog-foot"><span>Reply ➦</span><span>Comments ◯</span></div>
</div>
<div class="avatar abs" role="img" aria-label="Author portrait photo"></div>

<footer class="footer abs"></footer>
<div class="footer-mark abs"></div>
<div class="footer-name footer-text abs">Valdo Capital</div>
<div class="social abs" aria-label="Social media links"><i></i><i></i><i></i><i></i><i></i></div>

<div class="sitemap footer-text abs">
  <h4 class="footer-heading">Site Map</h4>
  <ul><li>Home</li><li>About Us</li><li>Investment Fields</li><li>Partners</li><li>News/Info</li><li>Valdo Blog</li></ul>
</div>
<div class="divider abs" style="left:359px"></div>
<div class="contact footer-text abs">
  <h4 class="footer-heading">Contact Us</h4>
  <div class="contact-row first"><svg width="10" height="9" viewBox="0 0 10 9"><polygon points="5,0 10,4.5 8.5,4.5 8.5,9 1.5,9 1.5,4.5 0,4.5" fill="#fff"/></svg><span>E 728, North Block, KMO Centre, East Sector, Shenzhen Bright Science Campus</span></div>
  <div class="contact-row"><svg width="10" height="9" viewBox="0 0 10 9"><path d="M2 0h2l1 2.5-1.3 1a5 5 0 0 0 2 2l1-1.3L9 5.5v2L8 9C4 8.5 1 5.5 1 1z" fill="#fff"/></svg><span>+86 0755 63920417</span></div>
  <div class="contact-row"><svg width="10" height="9" viewBox="0 0 10 9"><rect x="2" y="0" width="6" height="9" rx="1" fill="#fff"/><rect x="3" y="1.5" width="4" height="5" fill="#262626"/></svg><span>+86 13957280316</span></div>
</div>
<div class="divider abs" style="left:519px"></div>
<div class="find-us abs"><h4 class="footer-heading">Find Us</h4></div>
<div class="map abs" role="img" aria-label="Street map showing the office location"></div>

<div class="footer-bottom abs">Copyright © 2014 Valdo Capital . All rights reserved.</div>

</body>
</html>
```